Trabworth Business Cards

We need a business card design for Trabworth Mining.

This is a B2B company that buys and sells large machinery tires within the coal mining industry. The design should the strong, crisp and masculine. I have uploaded the company logo and rough mock-up of what the back of the card should look like. the front of the card should have the same look/feel as the back. I need editable templates for both the front and the back of the card.

Color scheme should be grey/green/black

Contact information to include on the card:
Name: Dale Pembrose
Title: Managing Director
Phone: 555-314-2069
Address: 1187 Welford #3 Dallas, TX 75290
Email: Dale@Trabworth-example.com

I am also opening a contest for letterhead design. If you submit a business card design, please also submit a letterhead design with the same look/feel. The winner of the business card design will also will the letter head and be paid for both.

Target Market(s)

Procurement men/women in the coal mining industry

Industry/Entity Type

Coal Mining

```html
<!DOCTYPE html>
<html lang="en">
<head>
<meta charset="utf-8">
<title>Trabworth Mining Stationery</title>
<link href="https://fonts.googleapis.com/css2?family=Oswald:wght@400;500&family=Open+Sans:wght@400;600&display=swap" rel="stylesheet">
<style>
:root{
  --board:#2a2a2a;
  --board-dark:#161616;
  --green:#6cb33f;
  --green-soft:#cfe3bf;
  --card-dark:#1e2219;
  --card-olive:#3f4a2a;
  --grey:#9a9a9a;
  --paper:#ffffff;
  --ink:#111111;
  --white:#f2f2f2;
}
*{margin:0;padding:0;box-sizing:border-box}
html,body{width:1200px;height:1000px;overflow:hidden}
body{background:var(--board-dark)}
.board{position:relative;width:1200px;height:1000px;
  background:radial-gradient(ellipse at 60% 40%,#3a3a3a 0%,var(--board) 45%,var(--board-dark) 100%)}
.brand-name{font-family:"Oswald",sans-serif;font-weight:500;letter-spacing:.06em;text-transform:uppercase;display:flex;align-items:center;white-space:nowrap}
.brand-mark{display:inline-block;background:var(--green);margin-right:.35em;flex:none}

/* letterhead */
.letterhead{position:absolute;left:68px;top:52px;width:507px;height:658px;background:var(--paper);box-shadow:0 6px 18px rgba(0,0,0,.6);overflow:hidden}
.letterhead .brand-head{position:absolute;left:0;right:0;top:30px;justify-content:center;font-size:26px;color:var(--ink)}
.letterhead .brand-head .brand-mark{width:22px;height:22px}
.letterhead .rule{position:absolute;left:0;right:0;top:77px;height:2px;background:var(--green)}
.letterhead .contact-line{position:absolute;left:0;right:0;top:84px;text-align:center;font-family:"Oswald",sans-serif;font-size:6px;letter-spacing:.08em;color:var(--green)}
.letter{font-family:"Open Sans",sans-serif;font-size:8.6px;line-height:12px;color:var(--ink)}
.letter-date{position:absolute;right:27px;top:130px;font-weight:600}
.letter-body{position:absolute;left:70px;top:176px;width:410px}
.letter-body p{margin-bottom:12px}
.letter-body p.tight{margin-bottom:0}
.letter-contact{position:absolute;left:68px;top:470px}
.side-strip{position:absolute;left:0;width:22px}
.letterhead .brand-foot{position:absolute;left:0;right:0;top:626px;justify-content:center;font-size:11px;color:var(--ink)}
.letterhead .brand-foot .brand-mark{width:10px;height:10px}

/* envelope */
.envelope{position:absolute;left:68px;top:718px;width:538px;height:247px;background:var(--paper);box-shadow:0 6px 18px rgba(0,0,0,.6);overflow:hidden}
.envelope .brand-name{position:absolute;left:20px;top:14px;font-size:19px;color:var(--ink)}
.envelope .brand-mark{width:16px;height:16px}
.envelope .return-address{position:absolute;left:56px;top:44px;font-family:"Oswald",sans-serif;font-size:7px;letter-spacing:.04em;color:var(--ink)}
.envelope .window{position:absolute;left:48px;top:132px;width:184px;height:58px;border-radius:8px;background:linear-gradient(#c9c9c9,#e6e6e6);box-shadow:inset 0 2px 4px rgba(0,0,0,.35)}

/* standalone brand */
.brand-hero{position:absolute;left:618px;top:72px;font-size:44px;letter-spacing:.05em;color:var(--white)}
.brand-hero .brand-mark{width:40px;height:40px}

/* business cards */
.card{position:absolute;left:665px;width:473px;box-shadow:0 8px 20px rgba(0,0,0,.7);overflow:hidden}
.card-front{top:225px;height:270px}
.card-back{top:548px;height:267px}
.card-texture{position:absolute;inset:0;background:radial-gradient(ellipse at 75% 25%,var(--card-olive) 0%,#2b3220 45%,var(--card-dark) 100%)}
.card .brand-name{position:absolute;font-size:30px;color:var(--white)}
.card .brand-mark{width:24px;height:24px}
.card-front .brand-name{left:57px;top:28px}
.card-back .brand-name{left:16px;top:205px}
.holder-name{position:absolute;left:40px;top:100px;font-family:"Oswald",sans-serif;font-size:20px;letter-spacing:.05em;color:var(--white);text-transform:uppercase}
.holder-title{position:absolute;left:40px;top:124px;font-family:"Oswald",sans-serif;font-size:13px;letter-spacing:.06em;color:var(--green);text-transform:uppercase}
.contact-list{position:absolute;left:36px;top:165px;list-style:none;font-family:"Oswald",sans-serif;font-size:10.5px;letter-spacing:.05em;color:var(--white)}
.contact-list li{display:flex;align-items:flex-start;margin-bottom:8px;line-height:12px}
.contact-list svg{width:12px;height:12px;margin-right:8px;flex:none}
.card-band{position:absolute;left:0;right:0;bottom:3px;height:13px;background:var(--green)}
</style>
</head>
<body>
<main class="board">

  <section class="letterhead" aria-label="Trabworth Mining letterhead">
    <div class="brand-name brand-head"><span class="brand-mark"></span>Trabworth Mining</div>
    <div class="rule"></div>
    <div class="contact-line">555-314-2069 &nbsp;|&nbsp; 1187 WELFORD #3 DALLAS, TX 75290 &nbsp;|&nbsp; TRABWORTH-EXAMPLE.COM</div>

    <div class="letter letter-date">Wednesday, October 09, 2013</div>
    <div class="letter letter-body">
      <p>We need a business card design for Trabworth Mining.</p>
      <p>This is a B2B company that buys and sells large machinery tires within the coal mining industry. The design should the strong, crisp and masculine. I have uploaded the company logo and rough mock-up of what the back of the card should look like. the front of the card should have the same look/feel as the back. I need editable templates for both the front and the back of the card.</p>
      <p>Color scheme should be grey/green/black</p>
      <p style="margin-top:24px" class="tight">I am also opening a contest for letterhead design. If you submit a business card design, please also submit a letterhead design with the same look/feel. The winner of the business card design will also will the letter head and be paid for both.</p>
      <p class="tight">Deadline</p>
      <p class="tight">Wednesday, October 09, 2013</p>
      <p class="tight">Target Market(s)</p>
      <p class="tight">Procurement men/women in the coal mining industry</p>
      <p class="tight">Look and Feel</p>
      <p class="tight">Each slider illustrates characteristics of the customer's brand and the style your design should communicate.</p>
    </div>
    <div class="letter letter-contact">
      Contact information to include on the card:<br>
      Name: Dale Pembrose<br>
      Title: Managing Director<br>
      Phone: 555-314-2069<br>
      Address: 1187 Welford #3 Dallas, TX 75290<br>
      Email: Dale@Trabworth-example.com
    </div>

    <div class="side-strip" style="top:489px;height:59px;background:var(--green)"></div>
    <div class="side-strip" style="top:548px;height:20px;background:var(--ink)"></div>
    <div class="side-strip" style="top:568px;height:90px;background:var(--grey)"></div>

    <div class="brand-name brand-foot"><span class="brand-mark"></span>Trabworth Mining</div>
  </section>

  <section class="envelope" aria-label="Trabworth Mining envelope">
    <div class="brand-name"><span class="brand-mark"></span>Trabworth Mining</div>
    <div class="return-address">1187 WELFORD #3 DALLAS, TX 75290</div>
    <div class="side-strip" style="top:80px;height:34px;background:var(--grey)"></div>
    <div class="side-strip" style="top:114px;height:18px;background:var(--ink)"></div>
    <div class="side-strip" style="top:132px;height:115px;background:var(--green)"></div>
    <div class="window"></div>
  </section>

  <div class="brand-name brand-hero"><span class="brand-mark"></span>Trabworth Mining</div>

  <section class="card card-front" aria-label="Business card front">
    <div class="card-texture" role="img" aria-label="Dark green and black scratched grunge texture"></div>
    <div class="brand-name"><span class="brand-mark"></span>Trabworth Mining</div>
    <div class="holder-name">Dale Pembrose</div>
    <div class="holder-title">Managing Director</div>
    <ul class="contact-list">
      <li><svg viewBox="0 0 12 12"><circle cx="6" cy="6" r="6" fill="#6cb33f"/><path d="M4 3.2l1 1.6-.6.7a4 4 0 0 0 2.1 2.1l.7-.6 1.6 1-.5 1A4.8 4.8 0 0 1 3 4.1z" fill="#1e2219"/></svg>: 555.314.2069</li>
      <li><svg viewBox="0 0 12 12"><circle cx="6" cy="6" r="6" fill="#6cb33f"/><rect x="3" y="4" width="6" height="4.2" fill="none" stroke="#1e2219" stroke-width=".9"/><path d="M3 4l3 2.4L9 4" fill="none" stroke="#1e2219" stroke-width=".9"/></svg>: DALE@TRABWORTH-EXAMPLE.COM</li>
      <li><svg viewBox="0 0 12 12"><circle cx="6" cy="6" r="6" fill="#6cb33f"/><path d="M6 2.5a2.2 2.2 0 0 1 2.2 2.2C8.2 6.4 6 9.5 6 9.5S3.8 6.4 3.8 4.7A2.2 2.2 0 0 1 6 2.5z" fill="#1e2219"/><circle cx="6" cy="4.7" r=".8" fill="#6cb33f"/></svg><span>: 1187 WELFORD #3<br>&nbsp;&nbsp;DALLAS, TX 75290</span></li>
    </ul>
    <div class="card-band"></div>
  </section>

  <section class="card card-back" aria-label="Business card back">
    <div class="card-texture" role="img" aria-label="Dark green and black scratched grunge texture"></div>
    <div class="brand-name"><span class="brand-mark"></span>Trabworth Mining</div>
  </section>

</main>
</body>
</html>
```